Delivery Performance Dashboard for Web Portal

We need you to design a dashboard for our web portal. We deliver sand and stone to construction jobsites. The attached screenshot is from our current web portal dashboard . It shows how much material has been delivered from an order.

Loadline will deliver multiple loads during the day and the dispatcher uses the dashboard to monitor if they need to add more trucks or less trucks to fulfill the order. An example would be, I need to ship 1,000 tons of sand to a jobsite and I plan to use 10 trucks during the day and that it will take 10 hours of hauling to complete the job. After 5 hours of hauling (50% the day is over), I should have delivered 500 tons of sand (50% of the order). But maybe there is a lot of traffic, and I only have delivered 300 tons. The dashboard will show that I am behind schedule and I might need to add 2 more trucks to the job.

Industry/Entity Type

Construction

Font styles to use
Sans Serif

Requirements
Must have
• We need a progress bar showing how much material has been delivered, how much material was requested to be delivered total and how much material should have been delivered at the current time. The goal is to show the user if the deliveries are ahead or behind the expected pace and why.
Nice to have
• The icons for plant, driving and jobsite show if the actual times have exceeded or beaten the planned times. Maybe you have other ideas to show the user if the trucks are sitting longer on the jobsite, at the plant to get loaded or driving to and from the jobsite.

```html
<!DOCTYPE html>
<html lang="en">
<head>
<meta charset="utf-8">
<title>Loadline – Delivery Dashboard</title>
<link href="https://fonts.googleapis.com/css2?family=Poppins:wght@400;500;600&family=Source+Sans+3:wght@400;600&display=swap" rel="stylesheet">
<style>
:root{
  --stage:#1c2838;
  --panel:#4a93ef;
  --navy:#2d5699;
  --side:#2f5597;
  --side-line:#264a86;
  --ink:#3a3f47;
  --muted:#6b7380;
  --row-alt:#f6f6f6;
  --line:#e6e8ec;
  --brand:#2a55a8;
  --green:#7cb342;
  --red:#e5531c;
  --blue:#2f6bc4;
  --accent:#3f8ae6;
}
*{box-sizing:border-box;margin:0;padding:0}
html,body{width:1044px;height:1200px;overflow:hidden;background:var(--stage);font-family:"Source Sans 3",Arial,sans-serif;color:var(--ink)}
.screen{position:absolute;left:73px;width:897px;height:510px;background:var(--panel);overflow:hidden}
.screen.first{top:70px}.screen.second{top:618px}
.topbar{position:absolute;left:0;top:0;width:100%;height:39px;background:#fff;display:flex;align-items:center;padding:0 0 0 17px}
.brand{font-family:"Poppins",sans-serif;font-weight:600;font-size:17px;color:var(--brand);letter-spacing:.3px}
.user{position:absolute;left:665px;top:10px;display:flex;align-items:center;gap:7px;font-family:"Poppins",sans-serif;font-size:6px;font-weight:600;color:#222}
.avatar{width:19px;height:19px;border-radius:50%;background:radial-gradient(circle at 50% 40%,#9aa7b4,#3d4d60)}
.toplink{position:absolute;top:13px;display:flex;align-items:center;gap:5px;font-family:"Poppins",sans-serif;font-size:7px;color:#444}
.toplink svg{width:10px;height:10px}
.settings{left:756px}.logout{left:817px}
.sidebar{position:absolute;left:0;top:39px;width:37px;bottom:0;background:var(--side)}
.nav-item{height:36px;border-bottom:1px solid var(--side-line);display:flex;align-items:center;justify-content:center}
.nav-item.active{background:var(--panel)}
.nav-item svg{width:11px;height:11px;fill:#fff}
.card{position:absolute;left:72px;top:66px;width:790px;height:385px;background:#fff}
.grid{display:grid;grid-template-columns:50px 89px 109px 135px 63px 151px 91px 56px 46px}
.thead{height:31px;background:var(--navy);font-family:"Poppins",sans-serif;font-size:6px;font-weight:500;color:#fff;align-items:center}
.thead span{padding-left:15px;display:flex;align-items:center;gap:3px}
.thead svg{width:7px;height:7px;stroke:#fff;fill:none}
.row{height:44px;align-items:center;font-size:6.3px;color:var(--ink);position:relative}
.row.alt{background:var(--row-alt)}
.row.focus{background:#fff;box-shadow:0 2px 8px rgba(40,70,120,.25);outline:1px solid #c9dcf5;z-index:2}
.row>div{height:100%;display:flex;align-items:center;padding-left:15px;border-right:1px solid var(--line)}
.row>div:last-child{border-right:0}
.tons{flex-direction:column;align-items:stretch!important;justify-content:center;padding:0 16px 0 24px!important;gap:6px}
.track{position:relative;height:3px;background:#e3e8ef;border-radius:2px}
.fill{position:absolute;left:0;top:0;height:3px;width:58%;background:var(--accent);border-radius:2px}
.knob{position:absolute;left:58%;top:-1.5px;width:5px;height:5px;margin-left:-2.5px;border-radius:50%;background:var(--brand)}
.tons-meta{display:flex;justify-content:space-between;font-size:5.6px}
.wait{gap:5px;padding-left:14px!important}
.wait svg{width:9px;height:9px;stroke:#556;fill:none;stroke-width:1.2}
.caret{width:0;height:0;border-left:2px solid transparent;border-right:2px solid transparent;border-top:2.5px solid #445;margin-left:-2px}
.boxed{display:flex;align-items:center;gap:4px;border:1px solid #d6dae0;border-radius:2px;padding:2px 4px;background:#fff}
.rem{font-weight:600;padding-left:11px!important}
.rem.ahead{color:var(--green)}.rem.behind{color:var(--red)}.rem.even{color:var(--blue)}
.delta{font-weight:600;padding-left:15px!important}
.pager{position:absolute;left:325px;top:330px;display:flex;gap:4px;align-items:flex-end}
.pager span{width:13px;height:13px;border:1px solid #d5d9df;font-size:5.5px;display:flex;align-items:center;justify-content:center;color:#444;background:#fff}
.pager .nav{background:var(--navy);border-color:var(--navy)}
.pager .nav.next{background:var(--accent);border-color:var(--accent)}
.pager .dots{border:0;width:6px;height:6px;background:none}
.pager svg{width:5px;height:5px;fill:#fff}
.footer{position:absolute;top:480px;left:0;width:100%;text-align:center;font-family:"Poppins",sans-serif;font-size:6px;color:#fff}
.popover{position:absolute;left:611px;top:63px;width:136px;height:190px;background:#fff;box-shadow:0 3px 12px rgba(20,40,80,.3);z-index:5;font-family:"Poppins",sans-serif;font-size:5px;color:#333}
.pop-head{height:17.5px;background:#2f78d9;color:#fff;font-size:6px;display:flex;align-items:center;justify-content:center}
.pop-cycle{height:21px;display:flex;align-items:center;justify-content:space-between;padding:0 10px 0 11px;border-bottom:1px solid var(--line)}
.pop-cycle svg{width:18px;height:9px;stroke:var(--brand);fill:none;stroke-width:1}
.stage{height:38px;padding:6px 10px 0 10px;border-bottom:1px solid var(--line);position:relative}
.stage.tint{background:#eef3fa}
.stage-name{display:flex;align-items:center;gap:5px;font-size:5.2px;font-weight:500}
.stage-name svg{width:14px;height:12px;stroke:var(--accent);fill:none;stroke-width:1}
.stage-vals{position:absolute;left:10px;right:10px;bottom:6px;display:flex;justify-content:space-between;font-size:4.8px}
.stage:last-child{border-bottom:0}
</style>
</head>
<body>
<svg width="0" height="0" style="position:absolute">
  <defs>
    <symbol id="i-plant" viewBox="0 0 12 12"><path d="M1 11h10M2 11V6l3 2V6l3 2V2h2v9"/></symbol>
    <symbol id="i-truck" viewBox="0 0 12 12"><path d="M1 3h6v5H1zM7 5h2.5L11 7v1H7"/><circle cx="3" cy="9.5" r="1"/><circle cx="9" cy="9.5" r="1"/></symbol>
    <symbol id="i-pin" viewBox="0 0 12 12"><path d="M6 8s3-3 3-5a3 3 0 0 0-6 0c0 2 3 5 3 5zM2 11h8"/><circle cx="6" cy="3" r="1"/></symbol>
    <symbol id="i-equip" viewBox="0 0 14 12"><path d="M1 11h7V6H1zM3 6V4h3v2M8 8l4-6 1 2M3 11v-1M6 11v-1"/></symbol>
    <symbol id="i-clock" viewBox="0 0 10 10"><circle cx="5" cy="5" r="4"/><path d="M5 2.5V5l2 1"/></symbol>
  </defs>
</svg>

<!-- Screen: table overview -->
<section class="screen first">
  <header class="topbar">
    <div class="brand">Loadline</div>
    <div class="user"><div class="avatar" role="img" aria-label="User profile photo"></div>Dana Whitfield</div>
    <div class="toplink settings"><svg viewBox="0 0 10 10" fill="none" stroke="#5a7fc0"><circle cx="5" cy="5" r="1.6"/><circle cx="5" cy="5" r="3.6" stroke-dasharray="2 1"/></svg>Settings</div>
    <div class="toplink logout"><svg viewBox="0 0 10 10" fill="none" stroke="#5a7fc0"><rect x="1" y="1" width="8" height="8"/><path d="M3.5 3.5l3 3M6.5 3.5l-3 3"/></svg>Logout</div>
  </header>
  <nav class="sidebar">
    <div class="nav-item"><svg viewBox="0 0 12 12"><rect x="0" y="1" width="2.5" height="2.5"/><rect x="3.2" y="1" width="2.5" height="2.5"/><rect x="6.4" y="1" width="2.5" height="2.5"/><rect x="9.6" y="1" width="2.4" height="2.5"/><rect x="0" y="4.7" width="2.5" height="2.5"/><rect x="3.2" y="4.7" width="2.5" height="2.5"/><rect x="6.4" y="4.7" width="2.5" height="2.5"/><rect x="9.6" y="4.7" width="2.4" height="2.5"/><rect x="0" y="8.4" width="2.5" height="2.5"/><rect x="3.2" y="8.4" width="2.5" height="2.5"/><rect x="6.4" y="8.4" width="2.5" height="2.5"/><rect x="9.6" y="8.4" width="2.4" height="2.5"/></svg></div>
    <div class="nav-item active"><svg viewBox="0 0 12 12"><path d="M2 0h6l3 3v9H2z"/></svg></div>
    <div class="nav-item"><svg viewBox="0 0 12 12"><rect x="4" y="1" width="7" height="6"/><rect x="1" y="5" width="6" height="6"/></svg></div>
    <div class="nav-item"><svg viewBox="0 0 12 12"><circle cx="2" cy="10" r="1.5"/><path d="M1 5a6 6 0 0 1 6 6H5.5A4.5 4.5 0 0 0 1 6.5zM1 1a10 10 0 0 1 10 10H9.5A8.5 8.5 0 0 0 1 2.5z"/></svg></div>
    <div class="nav-item"><svg viewBox="0 0 12 12"><path d="M0 1h12v10H0zM1.5 3.5v6h9v-6z"/></svg></div>
    <div class="nav-item"><svg viewBox="0 0 12 12"><rect x="0" y="1.5" width="2" height="1.5"/><rect x="3" y="1.5" width="9" height="1.5"/><rect x="0" y="5" width="2" height="1.5"/><rect x="3" y="5" width="9" height="1.5"/><rect x="0" y="8.5" width="2" height="1.5"/><rect x="3" y="8.5" width="9" height="1.5"/></svg></div>
    <div class="nav-item"><svg viewBox="0 0 12 12"><path d="M0 1h12v8H4l-3 3V9H0zM2 3.5h8v1H2zM2 6h6v1H2z" fill-rule="evenodd"/></svg></div>
    <div class="nav-item"><svg viewBox="0 0 12 12"><path d="M0 0h12v12H0zM2 10h8L7 6 5 8.5 4 7z" fill-rule="evenodd"/></svg></div>
    <div class="nav-item"><svg viewBox="0 0 12 12"><path d="M3 0h9v9H3zM0 3h1.5v7.5H9V12H0zM5 2.5h5v1H5zM5 5h5v1H5z" fill-rule="evenodd"/></svg></div>
    <div class="nav-item"><svg viewBox="0 0 12 12"><rect x="0" y="0" width="5.5" height="7"/><rect x="6.5" y="0" width="5.5" height="4"/><rect x="0" y="8" width="5.5" height="4"/><rect x="6.5" y="5" width="5.5" height="7"/></svg></div>
    <div class="nav-item"><svg viewBox="0 0 12 12"><path d="M1 0h10v12H1zM3 3h6v1H3zM3 5.5h6v1H3zM3 8h6v1H3z" fill-rule="evenodd"/></svg></div>
    <div class="nav-item"></div>
  </nav>
  <main class="card">
    <div class="grid thead"><span>Order</span><span>Origin</span><span>Destination</span><span>Customer</span><span>Status</span><span>Tons</span><span>Wait Times</span><span>Remaining <svg><use href="#i-clock"/></svg></span><span>+/- <svg viewBox="0 0 12 12"><use href="#i-truck"/></svg></span></div>
    <div class="grid row"><div>17746</div><div>Ridgeview Asphalt Plant</div><div>KTRV -185 from mm 77 - 98</div><div>Harlan Construction - North Division</div><div>Accepted</div><div class="tons"><div class="track"><div class="fill"></div><div class="knob"></div></div><div class="tons-meta"><span>722.57 / 1500</span><span>7:30am - 5:00pm</span></div></div><div class="wait"><svg><use href="#i-plant"/></svg><i class="caret"></i><span class="boxed"><svg><use href="#i-truck"/></svg><i class="caret"></i></span><svg><use href="#i-pin"/></svg><i class="caret"></i></div><div class="rem ahead">+1:25 hrs</div><div class="delta">-31</div></div>
    <div class="grid row alt"><div>17746</div><div>Millbrook Asphalt</div><div>Cedar Springs</div><div>Harlan Construction - North Division</div><div>Accepted</div><div class="tons"><div class="track"><div class="fill"></div><div class="knob"></div></div><div class="tons-meta"><span>722.57 / 1500</span><span>7:30am - 5:00pm</span></div></div><div class="wait"><svg><use href="#i-plant"/></svg><i class="caret"></i><span class="boxed"><svg><use href="#i-truck"/></svg><i class="caret"></i></span><svg><use href="#i-pin"/></svg><i class="caret"></i></div><div class="rem behind">-0:28 hrs</div><div class="delta">+16</div></div>
    <div class="grid row focus"><div>17746</div><div>Ridgeview Asphalt Plant</div><div>KTRV -185 from mm 77 - 98</div><div>Harlan Construction - North Division</div><div>Accepted</div><div class="tons"><div class="track"><div class="fill"></div><div class="knob"></div></div><div class="tons-meta"><span>722.57 / 1500</span><span>7:30am - 5:00pm</span></div></div><div class="wait"><svg><use href="#i-plant"/></svg><i class="caret"></i><span class="boxed"><svg><use href="#i-truck"/></svg><i class="caret"></i></span><svg><use href="#i-pin"/></svg><i class="caret"></i></div><div class="rem even">8:00 hrs</div><div class="delta">-31</div></div>
    <div class="grid row alt"><div>17746</div><div>Millbrook Asphalt</div><div>Cedar Springs</div><div>Harlan Construction - North Division</div><div>Accepted</div><div class="tons"><div class="track"><div class="fill"></div><div class="knob"></div></div><div class="tons-meta"><span>722.57 / 1500</span><span>7:30am - 5:00pm</span></div></div><div class="wait"><svg><use href="#i-plant"/></svg><i class="caret"></i><span class="boxed"><svg><use href="#i-truck"/></svg><i class="caret"></i></span><svg><use href="#i-pin"/></svg><i class="caret"></i></div><div class="rem behind">-0:28 hrs</div><div class="delta">+16</div></div>
    <div class="grid row"><div>17746</div><div>Ridgeview Asphalt Plant</div><div>KTRV -185 from mm 77 - 98</div><div>Harlan Construction - North Division</div><div>Accepted</div><div class="tons"><div class="track"><div class="fill"></div><div class="knob"></div></div><div class="tons-meta"><span>722.57 / 1500</span><span>7:30am - 5:00pm</span></div></div><div class="wait"><svg><use href="#i-plant"/></svg><i class="caret"></i><span class="boxed"><svg><use href="#i-truck"/></svg><i class="caret"></i></span><svg><use href="#i-pin"/></svg><i class="caret"></i></div><div class="rem ahead">+1:25 hrs</div><div class="delta">-31</div></div>
    <div class="grid row alt"><div>17746</div><div>Millbrook Asphalt</div><div>Cedar Springs</div><div>Harlan Construction - North Division</div><div>Accepted</div><div class="tons"><div class="track"><div class="fill"></div><div class="knob"></div></div><div class="tons-meta"><span>722.57 / 1500</span><span>7:30am - 5:00pm</span></div></div><div class="wait"><svg><use href="#i-plant"/></svg><i class="caret"></i><span class="boxed"><svg><use href="#i-truck"/></svg><i class="caret"></i></span><svg><use href="#i-pin"/></svg><i class="caret"></i></div><div class="rem even">8:00 hrs</div><div class="delta">+16</div></div>
    <div class="pager"><span class="nav"><svg viewBox="0 0 6 6"><path d="M4.5 0v6L1 3z"/></svg></span><span>1</span><span>2</span><span>3</span><span>4</span><span>5</span><span class="dots">…</span><span>10</span><span class="nav next"><svg viewBox="0 0 6 6"><path d="M1.5 0v6L5 3z"/></svg></span></div>
  </main>
  <footer class="footer">©2020 Loadline, All Rights Reserved.</footer>
</section>

<!-- Screen: wait time breakdown open -->
<section class="screen second">
  <header class="topbar">
    <div class="brand">Loadline</div>
    <div class="user"><div class="avatar" role="img" aria-label="User profile photo"></div>Dana Whitfield</div>
    <div class="toplink settings"><svg viewBox="0 0 10 10" fill="none" stroke="#5a7fc0"><circle cx="5" cy="5" r="1.6"/><circle cx="5" cy="5" r="3.6" stroke-dasharray="2 1"/></svg>Settings</div>
    <div class="toplink logout"><svg viewBox="0 0 10 10" fill="none" stroke="#5a7fc0"><rect x="1" y="1" width="8" height="8"/><path d="M3.5 3.5l3 3M6.5 3.5l-3 3"/></svg>Logout</div>
  </header>
  <nav class="sidebar">
    <div class="nav-item"><svg viewBox="0 0 12 12"><rect x="0" y="1" width="2.5" height="2.5"/><rect x="3.2" y="1" width="2.5" height="2.5"/><rect x="6.4" y="1" width="2.5" height="2.5"/><rect x="9.6" y="1" width="2.4" height="2.5"/><rect x="0" y="4.7" width="2.5" height="2.5"/><rect x="3.2" y="4.7" width="2.5" height="2.5"/><rect x="6.4" y="4.7" width="2.5" height="2.5"/><rect x="9.6" y="4.7" width="2.4" height="2.5"/><rect x="0" y="8.4" width="2.5" height="2.5"/><rect x="3.2" y="8.4" width="2.5" height="2.5"/><rect x="6.4" y="8.4" width="2.5" height="2.5"/><rect x="9.6" y="8.4" width="2.4" height="2.5"/></svg></div>
    <div class="nav-item active"><svg viewBox="0 0 12 12"><path d="M2 0h6l3 3v9H2z"/></svg></div>
    <div class="nav-item"><svg viewBox="0 0 12 12"><rect x="4" y="1" width="7" height="6"/><rect x="1" y="5" width="6" height="6"/></svg></div>
    <div class="nav-item"><svg viewBox="0 0 12 12"><circle cx="2" cy="10" r="1.5"/><path d="M1 5a6 6 0 0 1 6 6H5.5A4.5 4.5 0 0 0 1 6.5zM1 1a10 10 0 0 1 10 10H9.5A8.5 8.5 0 0 0 1 2.5z"/></svg></div>
    <div class="nav-item"><svg viewBox="0 0 12 12"><path d="M0 1h12v10H0zM1.5 3.5v6h9v-6z"/></svg></div>
    <div class="nav-item"><svg viewBox="0 0 12 12"><rect x="0" y="1.5" width="2" height="1.5"/><rect x="3" y="1.5" width="9" height="1.5"/><rect x="0" y="5" width="2" height="1.5"/><rect x="3" y="5" width="9" height="1.5"/><rect x="0" y="8.5" width="2" height="1.5"/><rect x="3" y="8.5" width="9" height="1.5"/></svg></div>
    <div class="nav-item"><svg viewBox="0 0 12 12"><path d="M0 1h12v8H4l-3 3V9H0zM2 3.5h8v1H2zM2 6h6v1H2z" fill-rule="evenodd"/></svg></div>
    <div class="nav-item"><svg viewBox="0 0 12 12"><path d="M0 0h12v12H0zM2 10h8L7 6 5 8.5 4 7z" fill-rule="evenodd"/></svg></div>
    <div class="nav-item"><svg viewBox="0 0 12 12"><path d="M3 0h9v9H3zM0 3h1.5v7.5H9V12H0zM5 2.5h5v1H5zM5 5h5v1H5z" fill-rule="evenodd"/></svg></div>
    <div class="nav-item"><svg viewBox="0 0 12 12"><rect x="0" y="0" width="5.5" height="7"/><rect x="6.5" y="0" width="5.5" height="4"/><rect x="0" y="8" width="5.5" height="4"/><rect x="6.5" y="5" width="5.5" height="7"/></svg></div>
    <div class="nav-item"><svg viewBox="0 0 12 12"><path d="M1 0h10v12H1zM3 3h6v1H3zM3 5.5h6v1H3zM3 8h6v1H3z" fill-rule="evenodd"/></svg></div>
    <div class="nav-item"></div>
  </nav>
  <main class="card">
    <div class="grid thead"><span>Order</span><span>Origin</span><span>Destination</span><span>Customer</span><span>Status</span><span>Tons</span><span>Wait Times</span><span>Remaining <svg><use href="#i-clock"/></svg></span><span>+/- <svg viewBox="0 0 12 12"><use href="#i-truck"/></svg></span></div>
    <div class="grid row"><div>17746</div><div>Ridgeview Asphalt Plant</div><div>KTRV -185 from mm 77 - 98</div><div>Harlan Construction - North Division</div><div>Accepted</div><div class="tons"><div class="track"><div class="fill"></div><div class="knob"></div></div><div class="tons-meta"><span>722.57 / 1500</span><span>7:30am - 5:00pm</span></div></div><div class="wait"><svg><use href="#i-plant"/></svg><i class="caret"></i><span class="boxed"><svg><use href="#i-truck"/></svg><i class="caret"></i></span><svg><use href="#i-pin"/></svg><i class="caret"></i></div><div class="rem ahead">+1:25 hrs</div><div class="delta">-31</div></div>
    <div class="grid row alt"><div>17746</div><div>Millbrook Asphalt</div><div>Cedar Springs</div><div>Harlan Construction - North Division</div><div>Accepted</div><div class="tons"><div class="track"><div class="fill"></div><div class="knob"></div></div><div class="tons-meta"><span>722.57 / 1500</span><span>7:30am - 5:00pm</span></div></div><div class="wait"></div><div class="rem"></div><div class="delta">+16</div></div>
    <div class="grid row focus"><div>17746</div><div>Ridgeview Asphalt Plant</div><div>KTRV -185 from mm 77 - 98</div><div>Harlan Construction - North Division</div><div>Accepted</div><div class="tons"><div class="track"><div class="fill"></div><div class="knob"></div></div><div class="tons-meta"><span>722.57 / 1500</span><span>7:30am - 5:00pm</span></div></div><div class="wait"></div><div class="rem"></div><div class="delta">-31</div></div>
    <div class="grid row alt"><div>17746</div><div>Millbrook Asphalt</div><div>Cedar Springs</div><div>Harlan Construction - North Division</div><div>Accepted</div><div class="tons"><div class="track"><div class="fill"></div><div class="knob"></div></div><div class="tons-meta"><span>722.57 / 1500</span><span>7:30am - 5:00pm</span></div></div><div class="wait"></div><div class="rem"></div><div class="delta">+16</div></div>
    <div class="grid row"><div>17746</div><div>Ridgeview Asphalt Plant</div><div>KTRV -185 from mm 77 - 98</div><div>Harlan Construction - North Division</div><div>Accepted</div><div class="tons"><div class="track"><div class="fill"></div><div class="knob"></div></div><div class="tons-meta"><span>722.57 / 1500</span><span>7:30am - 5:00pm</span></div></div><div class="wait"></div><div class="rem"></div><div class="delta">-31</div></div>
    <div class="grid row alt"><div>17746</div><div>Millbrook Asphalt</div><div>Cedar Springs</div><div>Harlan Construction - North Division</div><div>Accepted</div><div class="tons"><div class="track"><div class="fill"></div><div class="knob"></div></div><div class="tons-meta"><span>722.57 / 1500</span><span>7:30am - 5:00pm</span></div></div><div class="wait"><svg><use href="#i-plant"/></svg><i class="caret"></i><span class="boxed"><svg><use href="#i-truck"/></svg><i class="caret"></i></span><svg><use href="#i-pin"/></svg><i class="caret"></i></div><div class="rem even">8:00 hrs</div><div class="delta">+16</div></div>

    <aside class="popover">
      <div class="pop-head">Order 17746</div>
      <div class="pop-cycle"><svg viewBox="0 0 18 9"><path d="M1 3h16M14 1l3 2M17 6H1M4 8L1 6"/></svg><span>Avg Cycle Time: 2hr 27min</span></div>
      <div class="stage tint"><div class="stage-name"><svg viewBox="0 0 12 12"><use href="#i-plant"/></svg>Plant (min)</div><div class="stage-vals"><span>Planned: 30</span><span>Actual: 33</span></div></div>
      <div class="stage"><div class="stage-name"><svg viewBox="0 0 12 12"><use href="#i-truck"/></svg>Driving (min)</div><div class="stage-vals"><span>Planned: 60</span><span>Actual: 83</span></div></div>
      <div class="stage tint"><div class="stage-name"><svg viewBox="0 0 12 12"><use href="#i-pin"/></svg>Jobsite (min)</div><div class="stage-vals"><span>Planned: 30</span><span>Actual: 30</span></div></div>
      <div class="stage"><div class="stage-name"><svg viewBox="0 0 14 12"><use href="#i-equip"/></svg>Equipment (min)</div><div class="stage-vals"><span></span><span>Actual: -</span></div></div>
    </aside>

    <div class="pager"><span class="nav"><svg viewBox="0 0 6 6"><path d="M4.5 0v6L1 3z"/></svg></span><span>1</span><span>2</span><span>3</span><span>4</span><span>5</span><span class="dots">…</span><span>10</span><span class="nav next"><svg viewBox="0 0 6 6"><path d="M1.5 0v6L5 3z"/></svg></span></div>
  </main>
  <footer class="footer">©2020 Loadline, All Rights Reserved.</footer>
</section>
</body>
</html>
```